Web Design Project for a new download application :-)

We need a website design and a logo design for a new website and desktop application.
The Website will be www.Gruvlo.com
The installed application will be: Gruvlo

Gruvlo is a desktop application that searches and finds all kind of Media files (Movies, Games, Songs, software, etc..)
Gruvlo will also manage the download process for the selected files.
Gruvlo automates the whole search and download process.

User Flow:
users will initially visit the website.
user will download the application from the website
user will install the application on his computer.
user will run and use the application.

What makes our software special:
-Great search engine for searching media files.
-Very high speed downloads. maximum speeds.
-Allow used to Search by: file type, size, date, format
-Pause and resume downloads
-Get any file you want instantly.
-Unlimited Downloads.

We will need:
Logo
WebSite Design
Icons for the desktop application.

we need only PSDs - no codded pages are needed !

Design to the following screen Size & resolution: 1024 x 768

Target Market(s)

movies and music lovers.
users who download movies, games, softwares, music etc...

Industry/Entity Type

Software

Requirements
Must have
• must have download button

```html
<!DOCTYPE html>
<html lang="en">
<head>
<meta charset="utf-8">
<title>Gruvlo – Desktop Media Downloader</title>
<link rel="stylesheet" href="https://fonts.googleapis.com/css2?family=Arimo:wght@400;700&family=Open+Sans:ital,wght@0,400;0,600;1,400&display=swap">
<style>
  :root {
    --header-top: #4a7fc4;
    --header-bottom: #2c5e9f;
    --nav-active: #21a0e0;
    --hero-top: #d9edf8;
    --hero-bottom: #ffffff;
    --headline-blue: #3366a8;
    --headline-grey: #5a5a5a;
    --tick-green: #7fae3c;
    --btn-green-light: #7dd431;
    --btn-green-dark: #2a8a06;
    --feature-blue: #0a4aa8;
    --body-grey: #666666;
    --footer-bg: #000000;
    --footer-text: #8a8a8a;
    --footer-link: #3aa0f0;
    --dot-grey: #9a9a96;
    --dot-green: #6ab81e;
  }
  * { box-sizing: border-box; margin: 0; padding: 0; }
  html, body { width: 1200px; height: 826px; overflow: hidden; background: #fff; }
  body { font-family: "Arimo", Arial, sans-serif; }
  .page { position: relative; width: 1200px; height: 826px; overflow: hidden; }

  /* Header */
  .site-header {
    position: absolute; left: 0; top: 0; width: 1200px; height: 57px;
    background: linear-gradient(var(--header-top), var(--header-bottom));
    box-shadow: 0 2px 4px rgba(0,0,0,.25); z-index: 2;
  }
  .brand {
    position: absolute; left: 148px; top: 9px; display: flex; align-items: center; gap: 10px;
    color: #fff; font-family: "Open Sans", sans-serif; font-weight: 600; font-size: 31px; line-height: 38px;
  }
  .brand-mark { width: 28px; height: 24px; background: #fff; }
  .main-nav { position: absolute; left: 328px; top: 0; display: flex; height: 57px; }
  .main-nav a {
    display: block; height: 57px; line-height: 58px; padding: 0 17px;
    color: #fff; font-weight: 700; font-size: 13px; text-decoration: none;
  }
  .main-nav a.active { background: var(--nav-active); }
  .lang-select {
    position: absolute; left: 888px; top: 14px; width: 165px; height: 28px;
    background: #2a4f86; border: 1px solid #3c67a4; color: #c9d6ea; font-size: 12px;
    display: flex; align-items: center; padding-left: 8px; gap: 8px;
  }
  .lang-flag { width: 15px; height: 10px; background: #c8cfe0; border: 1px solid #b02030; }
  .lang-toggle {
    position: absolute; right: -1px; top: -1px; width: 19px; height: 28px; background: #5fa8e4;
    display: flex; align-items: center; justify-content: center;
  }

  /* Hero */
  .hero {
    position: absolute; left: 0; top: 57px; width: 1200px; height: 417px;
    background: linear-gradient(var(--hero-top), var(--hero-bottom) 70%, #eeeeee);
    border-bottom: 1px solid #d6d6d6;
  }
  .hero-art {
    position: absolute; left: 580px; top: 27px; width: 526px; height: 357px;
    background: radial-gradient(ellipse at 55% 60%, #f4ead8 0%, #f2c3a0 25%, #bfe2f3 55%, rgba(217,237,248,0) 75%);
  }
  .hero-title {
    position: absolute; left: 166px; top: 78px;
    font-family: "Open Sans", sans-serif; font-weight: 400; font-size: 24px; line-height: 32px;
    color: var(--headline-grey); text-shadow: 0 2px 3px rgba(0,0,0,.2);
  }
  .hero-title .name { color: var(--headline-blue); }
  .hero-points { position: absolute; left: 139px; top: 121px; list-style: none; }
  .hero-points li {
    display: flex; align-items: center; gap: 8px; height: 33.5px; white-space: nowrap;
    font-family: "Open Sans", sans-serif; font-size: 16.5px; color: var(--headline-grey);
    text-shadow: 0 2px 3px rgba(0,0,0,.18);
  }
  .hero-points em { font-style: italic; }
  .download-btn {
    position: absolute; left: 168px; top: 255px; width: 281px; height: 96px;
    border-radius: 10px; border: 3px solid #c9c9c9;
    background: linear-gradient(var(--btn-green-light), var(--btn-green-dark));
    box-shadow: 0 8px 10px -6px rgba(0,0,0,.4); color: #fff; text-decoration: none;
  }
  .download-btn .label {
    position: absolute; left: 22px; top: 16px; font-family: "Open Sans", sans-serif;
    font-weight: 600; font-size: 26px; letter-spacing: .5px; text-shadow: 0 1px 2px rgba(0,0,0,.35);
  }
  .download-btn .sub { position: absolute; left: 24px; top: 52px; font-size: 11px; line-height: 14px; }
  .download-btn .arrow-tab {
    position: absolute; right: 18px; top: -6px; width: 50px; height: 80px;
    background: linear-gradient(#ffffff, #d8d8d8); border-radius: 0 0 6px 6px;
    display: flex; align-items: flex-end; justify-content: center; padding-bottom: 8px;
  }
  .slider-dots { position: absolute; left: 554px; top: 384px; display: flex; gap: 5px; }
  .slider-dots span {
    width: 15px; height: 15px; border-radius: 50%; background: var(--dot-grey);
    box-shadow: inset 0 -2px 3px rgba(0,0,0,.3);
  }
  .slider-dots span.current { background: var(--dot-green); }

  /* Features */
  .features { position: absolute; left: 0; top: 474px; width: 1200px; height: 259px; }
  .feature { position: absolute; top: 46px; width: 270px; }
  .feature-search { left: 158px; }
  .feature-speed { left: 479px; }
  .feature-filter { left: 800px; }
  .feature-icon { position: absolute; left: 0; top: 0; width: 77px; height: 75px; border-radius: 8px; }
  .feature-title {
    position: absolute; left: 87px; top: 22px; width: 200px;
    color: var(--feature-blue); font-size: 16px; line-height: 19px; font-weight: 400;
  }
  .feature-text {
    position: absolute; left: 0; top: 94px; width: 250px;
    color: var(--body-grey); font-size: 13px; line-height: 22.5px;
  }
  .divider {
    position: absolute; top: 40px; width: 1px; height: 190px;
    background: linear-gradient(rgba(0,0,0,0), #dcdcdc 30%, #dcdcdc 70%, rgba(0,0,0,0));
    box-shadow: 4px 0 8px rgba(0,0,0,.06);
  }
  .slide-arrow { position: absolute; top: 112px; }
  .slide-prev { left: 79px; }
  .slide-next { left: 1097px; }

  /* Footer */
  .site-footer {
    position: absolute; left: 0; top: 733px; width: 1200px; height: 93px;
    background: var(--footer-bg); color: var(--footer-text); font-size: 13px;
  }
  .footer-nav { position: absolute; left: 188px; top: 27px; }
  .footer-nav a { color: var(--footer-text); text-decoration: none; }
  .footer-nav .sep { margin: 0 6px; }
  .copyright { position: absolute; left: 188px; top: 50px; }
  .copyright a { color: var(--footer-link); text-decoration: none; }
</style>
</head>
<body>
<div class="page">

  <header class="site-header">
    <div class="brand"><span class="brand-mark"></span>Gruvlo</div>
    <nav class="main-nav">
      <a href="#" class="active">HOME</a>
      <a href="#">DOWNLOAD</a>
      <a href="#">SUPPORT</a>
      <a href="#">AFFILIATES</a>
    </nav>
    <div class="lang-select">
      <span class="lang-flag"></span>English
      <span class="lang-toggle">
        <svg width="9" height="5" viewBox="0 0 9 5"><path d="M0 0h9L4.5 5z" fill="#1d3a66"/></svg>
      </span>
    </div>
  </header>

  <section class="hero">
    <div class="hero-art" role="img" aria-label="Illustration of an open cardboard box spilling media icons, film reels and albums under a rainbow with clouds and music notes"></div>
    <h1 class="hero-title"><span class="name">Gruvlo</span> is a desktop application that</h1>
    <ul class="hero-points">
      <li><svg width="22" height="20" viewBox="0 0 22 20"><path d="M2 11l6 7L20 2" fill="none" stroke="var(--tick-green)" stroke-width="2.5"/></svg><span><em>searches</em> and <em>finds</em> all kind of Media files</span></li>
      <li><svg width="22" height="20" viewBox="0 0 22 20"><path d="M2 11l6 7L20 2" fill="none" stroke="var(--tick-green)" stroke-width="2.5"/></svg><span><em>manages</em> the download process for the selected files</span></li>
      <li><svg width="22" height="20" viewBox="0 0 22 20"><path d="M2 11l6 7L20 2" fill="none" stroke="var(--tick-green)" stroke-width="2.5"/></svg><span><em>automates</em> the whole search and download process</span></li>
    </ul>
    <a href="#" class="download-btn">
      <span class="label">DOWNLOAD</span>
      <span class="sub">Download Gruvlo Application and<br>install it on your desktop</span>
      <span class="arrow-tab">
        <svg width="32" height="40" viewBox="0 0 32 40"><path d="M10 0h12v20h10L16 40 0 20h10z" fill="#3f9e12" stroke="#2a7a08"/></svg>
      </span>
    </a>
    <div class="slider-dots"><span class="current"></span><span></span><span></span><span></span><span></span></div>
  </section>

  <section class="features">
    <svg class="slide-arrow slide-prev" width="24" height="28" viewBox="0 0 24 28"><path d="M20 2L6 14l14 12" fill="none" stroke="#aaaaaa" stroke-width="5"/></svg>
    <div class="feature feature-search">
      <div class="feature-icon" role="img" aria-label="Icon of a film reel with a magnifying glass over a book" style="background:linear-gradient(#c9d6e2,#6b8fb3)"></div>
      <h2 class="feature-title">Great search engine for searching media files</h2>
      <p class="feature-text">Lorem ipsum dolor sit amet, consectetur adipiscing elit. Etiam auctor tortor tellus, ut consectetur arcu.</p>
    </div>
    <div class="feature feature-speed">
      <div class="feature-icon" role="img" aria-label="Icon of a green download arrow over a globe and drive" style="background:linear-gradient(#b8e08a,#5a86c0)"></div>
      <h2 class="feature-title">Very high speed downloads maximum speeds.</h2>
      <p class="feature-text">Lorem ipsum dolor sit amet, consectetur adipiscing elit. Etiam auctor tortor tellus, ut consectetur arcu.</p>
    </div>
    <div class="feature feature-filter">
      <div class="feature-icon" role="img" aria-label="Icon of a disc, music note and magnifying glass over documents" style="background:linear-gradient(#eeeeee,#a8c890)"></div>
      <h2 class="feature-title">Search by file type,<br>size, date, format</h2>
      <p class="feature-text">Lorem ipsum dolor sit amet, consectetur adipiscing elit. Etiam auctor tortor tellus, ut consectetur arcu.</p>
    </div>
    <div class="divider" style="left:439px"></div>
    <div class="divider" style="left:761px"></div>
    <svg class="slide-arrow slide-next" width="24" height="28" viewBox="0 0 24 28"><path d="M4 2l14 12L4 26" fill="none" stroke="#aaaaaa" stroke-width="5"/></svg>
  </section>

  <footer class="site-footer">
    <nav class="footer-nav">
      <a href="#">Home</a><span class="sep">|</span><a href="#">Download</a><span class="sep">|</span><a href="#">Support</a><span class="sep">|</span> <a href="#">Affiliates</a><span class="sep">|</span><a href="#">Contact Us</a><span class="sep">|</span><a href="#">Privacy Policy</a><span class="sep">|</span><a href="#">License Agreement</a>
    </nav>
    <p class="copyright">Copyright © <a href="#">Gruvlo.com</a> 2011.&nbsp; All rights reserved.</p>
  </footer>

</div>
</body>
</html>
```